Business card design for sustainable building and development company

Need a business card design for a new sustainable building and real estate development company in the San Francisco Bay area. Name of company is "Tovrin Advisors, LLC" and we provide "Sustainable building, energy and development services" for residential and non residential projects. We'd like the following colors used but not all area required: green, gray, blue. Design should communicate innovation, professionalism and sustainability. Our current website is www.tovrin-advisors.example. Another possible design idea is to have the following listed on the back of the card:
Certified: VERN QS, Eco Marker Rater, DOLM Rater, Terravue Inspector, KSO TQ Building Analyst. Its not a must but could be text that could be used for back of card. Overall, we are open to a simple, clean design and or one with more text than usual for a card.

Industry/Entity Type

Real Estate

Contact Information for Business Card

Name on card: Mark J. Halvik
Title for Name: Principal + Founder
Phone: 555.814.0627
Email: mhalvik@tovrin-advisors.example
Website: www.tovrin-advisors.example

Also, please add the following for address:
San Francisco, California

Requirements
Nice to have
• If you can integrate the outline of a skyline on the backside of the card and if it looks good, I would like to see the design
Should not have
• a barcode;

```html
<!DOCTYPE html>
<html lang="en">
<head>
<meta charset="utf-8">
<title>Tovrin Advisors — Business Card</title>
<link href="https://fonts.googleapis.com/css2?family=Exo+2:wght@400;500;600&family=Montserrat:wght@400;500;700&display=swap" rel="stylesheet">
<style>
  :root {
    --green: #6cbb4a;
    --paper: #f7f7f7;
    --paper-shade: #e6e6e6;
    --ink: #1c1c1c;
    --white: #ffffff;
    --backdrop: #e9e9e7;
  }
  * { margin: 0; padding: 0; box-sizing: border-box; }
  html, body {
    width: 1200px; height: 900px; overflow: hidden;
    background: var(--backdrop);
  }
  .card {
    position: absolute; left: 75px; top: 150px;
    width: 1050px; height: 600px;
    box-shadow: 0 14px 34px rgba(0,0,0,.22);
    overflow: hidden;
  }
  .card-shapes { position: absolute; inset: 0; }
  .contact {
    position: absolute; left: 64px; top: 60px;
    color: var(--white);
    font-family: "Exo 2", sans-serif;
  }
  .contact-name {
    font-size: 34px; font-weight: 500; letter-spacing: 2px;
    text-transform: uppercase; line-height: 1.1;
  }
  .contact-title { font-size: 20px; margin-top: 6px; letter-spacing: .5px; }
  .contact-address {
    font-size: 24px; line-height: 1.3; margin-top: 44px; letter-spacing: .5px;
  }
  .contact-list { list-style: none; margin-top: 50px; }
  .contact-list li {
    display: flex; align-items: center; gap: 14px;
    font-size: 20px; letter-spacing: 1px; height: 40px;
  }
  .contact-list li.small { font-size: 17px; letter-spacing: .3px; }
  .contact-list svg { width: 20px; height: 20px; flex: none; fill: var(--white); }
  .brand {
    position: absolute; left: 560px; top: 270px; width: 440px;
    display: flex; align-items: center; justify-content: center; gap: 16px;
  }
  .brand-dot {
    width: 22px; height: 22px; flex: none;
    border-radius: 50%; background: var(--green);
  }
  .brand-name {
    font-family: "Montserrat", sans-serif; font-weight: 700;
    font-size: 48px; color: var(--green); line-height: 1;
    letter-spacing: -.5px; white-space: nowrap;
  }
</style>
</head>
<body>
  <div class="card">
    <svg class="card-shapes" viewBox="0 0 1050 600" width="1050" height="600" aria-hidden="true">
      <defs>
        <linearGradient id="paperFade" x1="0" y1="0" x2="1" y2="1">
          <stop offset="0" stop-color="#f7f7f7"/>
          <stop offset="1" stop-color="#e6e6e6"/>
        </linearGradient>
      </defs>
      <rect width="1050" height="600" fill="#6cbb4a"/>
      <path d="M600 0 C 470 110, 420 380, 470 600 L1050 600 L1050 0 Z" fill="url(#paperFade)"/>
      <path d="M620 34 C 505 120, 470 340, 505 560 C 488 350, 520 160, 620 34 Z" fill="#1c1c1c"/>
    </svg>

    <div class="contact">
      <p class="contact-name">Mark J. Halvik</p>
      <p class="contact-title">Principal + Founder</p>
      <p class="contact-address">San Francisco,<br>California</p>
      <ul class="contact-list">
        <li>
          <svg viewBox="0 0 24 24"><path d="M6.6 10.8a15 15 0 0 0 6.6 6.6l2.2-2.2a1 1 0 0 1 1-.25 11.4 11.4 0 0 0 3.6.57 1 1 0 0 1 1 1V20a1 1 0 0 1-1 1A17 17 0 0 1 3 4a1 1 0 0 1 1-1h3.5a1 1 0 0 1 1 1c0 1.25.2 2.45.57 3.6a1 1 0 0 1-.25 1z"/></svg>
          555.814.0627
        </li>
        <li>
          <svg viewBox="0 0 24 24"><path d="M7 1h10a2 2 0 0 1 2 2v18a2 2 0 0 1-2 2H7a2 2 0 0 1-2-2V3a2 2 0 0 1 2-2zm0 3v14h10V4zm5 15.5a1 1 0 1 0 0 2 1 1 0 0 0 0-2z"/></svg>
          555.814.0627
        </li>
        <li>
          <svg viewBox="0 0 24 24"><path d="M3 2h18v20H3zm2 2v16h14V4zm2 2h10v3H7zm0 5h3v2H7zm5 0h5v2h-5zm-5 4h3v2H7zm5 0h5v2h-5z"/></svg>
          555.814.0627
        </li>
        <li class="small">
          <svg viewBox="0 0 24 24"><path d="M2 5h20v14H2zm2 2v.5l8 5.5 8-5.5V7zm0 2.9V17h16V9.9l-8 5.5z"/></svg>
          mhalvik@tovrin-advisors.example
        </li>
        <li class="small">
          <svg viewBox="0 0 24 24"><path d="M12 2a10 10 0 1 0 0 20 10 10 0 0 0 0-20zm-1 2.1V7H8.4A8 8 0 0 1 11 4.1zm2 0A8 8 0 0 1 15.6 7H13zM6.7 9H11v2H4.1a8 8 0 0 1 .6-2zm6.3 0h4.3a8 8 0 0 1 .6 2H13zm-8.9 4H11v2H4.7a8 8 0 0 1-.6-2zm8.9 0h6.9a8 8 0 0 1-.6 2H13zm-4.6 4H11v2.9A8 8 0 0 1 8.4 17zm4.6 0h2.6A8 8 0 0 1 13 19.9z"/></svg>
          www.tovrin-advisors.example
        </li>
      </ul>
    </div>

    <div class="brand">
      <span class="brand-dot" aria-hidden="true"></span>
      <p class="brand-name">Tovrin Advisors</p>
    </div>
  </div>
</body>
</html>
```